Flyer-Design für Vegane und Gluten freie Haarpflege
Zielgruppe
Herstellung + Vertrieb von VEGANEN Haarpflegeprodukten
Shampoo, Conditioner Gluten frei und Vegan nicht an Tieren getestet und biologisch abbaubar
Aufgabenstellung
DIN 4 Grösse 2 Seiten Produktinformation für Verbraucher

```html
<!DOCTYPE html>
<html lang="de">
<head>
<meta charset="utf-8">
<title>Vita Pura – Vegane Haarpflege</title>
<link rel="stylesheet" href="https://fonts.googleapis.com/css2?family=Jost:wght@300;400&family=Playfair+Display:ital@1&family=Roboto+Condensed:wght@300;400&display=swap">
<style>
  :root {
    --paper: #ffffff;
    --ink: #111111;
    --ink-soft: #3a3a3a;
    --brand-red: #a11d1a;
    --photo-light: #e3e3e3;
    --photo-grey: #d2d2d2;
    --photo-skin: #8a7468;
    --photo-dark: #1c1716;
    --pattern: #ececec;
    --bottle: #f4f4f4;
    --bottle-edge: #d2d2d2;
  }
  * { margin: 0; padding: 0; box-sizing: border-box; }
  html, body { width: 848px; height: 1200px; overflow: hidden; background: var(--paper); }
  .flyer { position: relative; width: 848px; height: 1200px; overflow: hidden; background: var(--paper); }

  .hero-photo {
    position: absolute; left: 0; top: 0; width: 848px; height: 516px;
    background:
      linear-gradient(180deg, rgba(30, 24, 22, 0) 50%, rgba(30, 24, 22, 0.45) 100%),
      linear-gradient(90deg, var(--photo-light) 0%, var(--photo-grey) 32%, var(--photo-skin) 52%, var(--photo-dark) 72%, var(--photo-dark) 100%);
  }
  .hero-quote {
    position: absolute; left: 40px; width: 530px; top: 402px;
    font-family: "Playfair Display", Georgia, serif; font-style: italic;
    font-size: 24px; line-height: 27px; color: #fff; text-align: center;
    text-transform: uppercase; letter-spacing: -0.6px;
    text-shadow: 0 1px 3px rgba(0, 0, 0, 0.45);
  }

  .pattern-field {
    position: absolute; left: 0; top: 516px; width: 848px; height: 684px;
    background: linear-gradient(180deg, var(--pattern) 0%, var(--paper) 35%, var(--pattern) 70%, var(--paper) 100%);
    opacity: 0.6;
  }

  .product-title {
    position: absolute; left: 59px; top: 546px;
    font-family: "Jost", sans-serif; font-weight: 300; font-size: 52px;
    letter-spacing: 1px; color: var(--ink); line-height: 1;
  }
  .claim-band {
    position: absolute; left: 0; top: 605px; width: 496px; height: 64px;
    background: var(--brand-red); color: #fff;
    font-family: "Jost", sans-serif; font-weight: 300; font-size: 24px;
    line-height: 30px; padding: 3px 0 0 60px; letter-spacing: 0.5px;
  }

  .info-text {
    position: absolute; left: 59px; top: 736px; width: 438px;
    font-family: "Roboto Condensed", sans-serif; font-weight: 300;
    font-size: 15.6px; line-height: 24.3px; color: var(--ink);
    text-transform: uppercase; text-align: justify;
  }

  .bottle {
    position: absolute; top: 677px; height: 486px;
    border-radius: 10px;
    background: linear-gradient(90deg, var(--bottle-edge) 0%, var(--bottle) 25%, #fff 55%, var(--bottle-edge) 100%);
  }
  .bottle--left { left: 530px; width: 132px; }
  .bottle--right { left: 686px; width: 116px; }

  .maker-name {
    position: absolute; left: 60px; top: 1105px;
    font-family: "Jost", sans-serif; font-weight: 400; font-size: 27px;
    letter-spacing: 5px; color: var(--ink-soft);
  }
</style>
</head>
<body>
<main class="flyer">
  <div class="hero-photo" role="img" aria-label="Foto: Frau mit langem, glänzend schwarzem Haar vor hellgrauem Hintergrund"></div>
  <p class="hero-quote">“Vita Pura Balance ist gluten frei<br>und vegan, nicht an Tieren getestet<br>und biologisch abbaubar”</p>

  <div class="pattern-field" role="img" aria-label="Dezentes hellgraues Ornamentmuster im Hintergrund"></div>

  <h1 class="product-title">VITA PURA</h1>
  <div class="claim-band">MIT EDLEN ROHSTOFFEN<br>AUS NACHHALTIGEN RESSOURCEN</div>

  <p class="info-text">Es ist ganz einfach, um Säure auszugleichen braucht man Base. Um Base zu neutralisieren benötigt man Säure. Daher muss man vor und nach dem Haare waschen immer einen pH-Ausgleich machen. Der Balancer ist ein Muss vor und nach jeglicher Kopf- und Haarwäsche um die Kopfhaut zu neutralisieren müssen Shampoos entweder etwas saurer oder basischer eingestellt sein, somit kann die Kopfhaut schon während der Reinigung auf den neutralen pH-Wert zurückgeführt werden.</p>

  <div class="bottle bottle--left" role="img" aria-label="Weiße Shampooflasche für geschädigtes Haar"></div>
  <div class="bottle bottle--right" role="img" aria-label="Zweite weiße Shampooflasche für geschädigtes Haar"></div>

  <p class="maker-name">LUKAS BRENNER</p>
</main>
</body>
</html>
```